Brovanek Data Yellow rose letterhead

I have a new logo for my company but in its current form it is too large to be used on letterhead or as a email signature. I need to have the designer use elements from the current logo and create something close to the original but more suited for smaller items.
Updates

I just uploaded a copy of our logo that does not have the weathered affect. Thanks

Reason: More time for revisions

Industry/Entity Type

It Company

Requirements
Must have
• The design must maintain the visual effect of the current logo. It needs to include the yellow rose and the name of the company.
Nice to have
• It would be nice to maintain the stamp theme and incorporate my name, address, phone, email. etc.

```html
<!DOCTYPE html>
<html lang="en">
<head>
<meta charset="utf-8">
<title>Brovanek Data Letterhead</title>
<link href="https://fonts.googleapis.com/css2?family=Open+Sans:ital,wght@0,600;0,700;1,400;1,600&display=swap" rel="stylesheet">
<style>
  :root {
    --paper: #ffffff;
    --band-brown: #5b4a42;
    --rose-gold: #f2c81c;
    --rose-soft: #fbe6a0;
    --ink-grey: #8a8580;
    --name-grey: #8c8782;
    --band-text: #ffffff;
    --mark-brown: #4a3a32;
  }
  html, body {
    margin: 0;
    padding: 0;
    overflow: hidden;
    background: var(--paper);
  }
  .letterhead {
    position: relative;
    width: 943px;
    height: 1200px;
    overflow: hidden;
    background: var(--paper);
    font-family: "Open Sans", Arial, sans-serif;
  }
  .brand-mark {
    position: absolute;
    left: 24px;
    top: 30px;
    width: 160px;
    display: flex;
    align-items: center;
    gap: 8px;
  }
  .brand-mark .mark-square {
    width: 14px;
    height: 14px;
    background: var(--rose-gold);
    flex: none;
  }
  .brand-mark .brand-name {
    font-weight: 700;
    font-size: 26px;
    line-height: 1.1;
    color: var(--mark-brown);
  }
  .tagline-band {
    position: absolute;
    left: 0;
    top: 160px;
    width: 943px;
    height: 42px;
    background: var(--band-brown);
    border-top: 1px solid var(--rose-gold);
    border-bottom: 1px solid var(--rose-gold);
    color: var(--band-text);
    font-weight: 700;
    font-size: 13.5px;
    z-index: 1;
  }
  .tagline-band .band-label {
    position: absolute;
    left: 26px;
    top: 12px;
    letter-spacing: -0.2px;
  }
  .tagline-band .band-slogan {
    position: absolute;
    left: 215px;
    top: 11px;
    font-size: 14.5px;
  }
  .header-divider {
    position: absolute;
    left: 194px;
    top: 0;
    width: 2px;
    height: 204px;
    background: var(--rose-gold);
    z-index: 2;
  }
  .contact-block {
    position: absolute;
    left: 218px;
    top: 14px;
    color: var(--ink-grey);
    font-style: italic;
    font-size: 16.5px;
    line-height: 19px;
  }
  .contact-block .person-name {
    font-weight: 600;
    font-size: 21px;
    letter-spacing: -0.5px;
    color: var(--name-grey);
    line-height: 28px;
  }
  .contact-block .email {
    margin-top: 19px;
  }
  .rose-decoration {
    position: absolute;
    left: 555px;
    top: 975px;
    width: 400px;
    height: 240px;
    background: radial-gradient(ellipse at 50% 50%, var(--rose-soft) 0%, rgba(251,230,160,0.65) 50%, rgba(255,255,255,0) 75%);
  }
</style>
</head>
<body>
<div class="letterhead">
  <div class="brand-mark">
    <span class="mark-square"></span>
    <span class="brand-name">Brovanek Data</span>
  </div>

  <div class="contact-block">
    <div class="person-name">Dr. Lena Marwick</div>
    <div>742 NW Cedar Ridge Rd, Ste. 1180</div>
    <div>Harlow Springs, TX 76510</div>
    <div>(800) 555-0147</div>
    <div class="email">lena@brovanek-data.com</div>
  </div>

  <div class="tagline-band">
    <span class="band-label">THE INSIGHT BUILDERS</span>
    <span class="band-slogan">Building Clearer Consumer Insights for Every Market</span>
  </div>

  <div class="header-divider"></div>

  <div class="rose-decoration" role="img" aria-label="Faint yellow rose illustration fading into the corner"></div>
</div>
</body>
</html>
```